new letterhead for my brokergae company KeelBright, Complete Marine Brokering

We need a new letterhead for our brokerage company called KeelBright. We are specialised in selling pleasure crafts (sailing and motoryachts). More info can be found at https://keelbright-example.com/en

I use this document for a quotation, a letter, sales agreement, selling instructions. I am looking for a cover page + a content page.

Th efollowing information needs to be in the header / footer; email, website, VAT number, Bank Account number, number chamber of ccomerce, registry number olpa, General terms and conditions TQRV apply.

```html
<!DOCTYPE html>
<html lang="en">
<head>
<meta charset="utf-8">
<title>KeelBright – Cover and Letter Page</title>
<link rel="stylesheet" href="https://fonts.googleapis.com/css2?family=Arimo:wght@400;700&family=Questrial&display=swap">
<style>
  :root{
    --brand-blue:#0f5ba1;
    --paper:#f3f3f3;
    --backdrop:#d9d9d9;
    --ink:#3a3a3a;
    --muted:#6b6b6b;
    --soft-grey:#cfcfcf;
    --deco-grey:#dedede;
    --white:#ffffff;
  }
  *{margin:0;padding:0;box-sizing:border-box}
  html,body{width:1200px;height:901px;overflow:hidden}
  body{background:var(--backdrop);font-family:"Arimo",Arial,sans-serif;color:var(--ink);position:relative}
  .sheet{position:absolute;top:105px;width:490px;height:692px;background:var(--paper);overflow:hidden}
  .sheet--cover{left:82px}
  .sheet--letter{left:630px}

  .contact{position:absolute;font-size:6.4px;line-height:8.4px;color:var(--ink)}
  .contact__group{border-left:1.5px solid var(--brand-blue);padding-left:6px}
  .contact__group + .contact__group{margin-top:6px}
  .contact__row{display:flex;align-items:center;gap:3px}
  .contact__row svg{width:6px;height:6px;flex:none}

  .brand{position:absolute;text-align:right;font-family:"Questrial",sans-serif;color:var(--brand-blue)}
  .brand__name{display:flex;align-items:center;justify-content:flex-end;gap:8px;line-height:1}
  .brand__dot{background:var(--brand-blue);border-radius:50%}
  .brand__tagline{text-transform:uppercase;font-weight:700;font-family:"Arimo",sans-serif}

  .cover__brand{left:150px;top:70px;width:296px}
  .cover__brand .brand__name{font-size:36px}
  .cover__brand .brand__dot{width:14px;height:14px}
  .cover__brand .brand__tagline{font-size:8.4px;letter-spacing:2.3px;margin-top:8px}

  .cover__band{position:absolute;left:0;top:169px;width:490px;height:240px;background:var(--brand-blue);color:var(--white)}
  .cover__meta{position:absolute;left:38px;top:65px;font-size:7.4px;line-height:8.8px}
  .cover__meta dt{font-weight:700}
  .cover__meta .cover__client{font-size:10px;line-height:12px;font-family:"Questrial",sans-serif}
  .cover__meta .cover__block{margin-top:10px;font-family:"Questrial",sans-serif}
  .cover__meta .cover__dates{margin-top:10px}
  .cover__title{position:absolute;right:39px;top:78px;text-align:right;font-family:"Questrial",sans-serif;font-weight:400;font-size:42px;line-height:43px;letter-spacing:.5px}
  .cover__rule{position:absolute;left:0;top:411px;width:490px;height:4px;background:var(--soft-grey)}
  .cover__decoration{position:absolute;left:107px;top:415px;width:383px;height:220px;background:radial-gradient(ellipse at 55% 55%,var(--deco-grey) 0%,var(--paper) 70%)}

  .legal{position:absolute;left:38px;right:38px;bottom:38px;font-size:5.4px;line-height:7.4px;color:var(--muted);text-align:left;border-left:1.5px solid var(--brand-blue);padding-left:6px}
  .legal strong{color:var(--brand-blue);font-weight:700}

  .footer{position:absolute;left:0;bottom:0;width:490px;height:30px}
  .footer svg{position:absolute;inset:0}
  .footer__url{position:absolute;right:37px;bottom:10px;color:var(--white);font-size:6.4px;letter-spacing:1.6px;white-space:nowrap}

  .letter__brand{left:38px;top:30px;width:150px;text-align:left}
  .letter__brand .brand__name{font-size:22px;justify-content:flex-start;gap:6px}
  .letter__brand .brand__dot{width:9px;height:9px}
  .letter__brand .brand__tagline{font-size:5.2px;letter-spacing:1.3px;margin-top:5px;padding-left:15px}
  .letter__contact{left:380px;top:34px}

  .letter__body{position:absolute;left:38px;top:182px;width:414px;font-size:6.9px;line-height:8.6px}
  .letter__date{margin-bottom:10px}
  .letter__address{margin-bottom:55px;font-style:normal}
  .letter__body p{text-align:justify;margin-bottom:8.6px}
  .letter__greeting{margin-bottom:6px!important}
  .letter__closing{display:flex;align-items:flex-start;gap:16px;margin-top:12px}
  .letter__signature{width:72px;height:40px;margin-top:-6px;background:linear-gradient(135deg,#e7e9f2,var(--paper))}
</style>
</head>
<body>

<section class="sheet sheet--cover" aria-label="Proposal cover page">
  <div class="contact" style="left:38px;top:89px">
    <div class="contact__group">Ankerweg 14<br>4870 AB Zeedorp</div>
    <div class="contact__group">
      <div class="contact__row"><svg viewBox="0 0 10 10"><path d="M2 1l2 0 1 2.5-1.2 1a5 5 0 0 0 2.7 2.7l1-1.2L10 7v2c-5 0-9-4-9-9z" fill="var(--brand-blue)"/></svg>+31 85 000 12 34</div>
      <div class="contact__row"><svg viewBox="0 0 10 10"><rect x="0.5" y="2" width="9" height="6" fill="var(--brand-blue)"/><path d="M0.5 2l4.5 3.5L9.5 2" stroke="#fff" stroke-width="0.8" fill="none"/></svg>info@keelbright-example.com</div>
      <div class="contact__row"><svg viewBox="0 0 10 10"><circle cx="5" cy="5" r="4.2" fill="none" stroke="var(--brand-blue)"/><path d="M1 5h8M5 1c-2 2.5-2 5.5 0 8M5 1c2 2.5 2 5.5 0 8" stroke="var(--brand-blue)" stroke-width="0.7" fill="none"/></svg>www.keelbright-example.com</div>
    </div>
  </div>

  <div class="brand cover__brand">
    <div class="brand__name"><span class="brand__dot"></span>KeelBright</div>
    <div class="brand__tagline">Complete Marine Brokering</div>
  </div>

  <div class="cover__band">
    <dl class="cover__meta">
      <dt>Prepared for:</dt>
      <dd class="cover__client">Pieter Vos</dd>
      <dd class="cover__block">Harbor Crest LLC<br>45 Quay Lane, Port Town, 4000<br>P: 0100 000 000 · E info@harborcrest-example.com</dd>
      <dt class="cover__dates">Proposal Issued:</dt>
      <dd>11.11.2017</dd>
      <dt class="cover__dates">Proposal Valid to:</dt>
      <dd>01.12.2017</dd>
    </dl>
    <h1 class="cover__title">BUSINESS<br>PROPOSAL</h1>
  </div>
  <div class="cover__rule"></div>
  <div class="cover__decoration" role="img" aria-label="Large faint brand watermark decoration"></div>

  <div class="legal">
    VAT NL000000000B01 · IBAN NL00 BANK 0000 0000 00 · Chamber of Commerce 00000000 · Registry number olpa 0000-00<br>
    <strong>General terms and conditions TQRV apply.</strong>
  </div>

  <footer class="footer">
    <svg viewBox="0 0 490 30" preserveAspectRatio="none">
      <rect x="0" y="8" width="330" height="4" fill="var(--soft-grey)"/>
      <path d="M0 30H490V2H345C325 2 320 18 300 26L0 26Z" fill="var(--brand-blue)"/>
    </svg>
    <span class="footer__url">www.keelbright-example.com</span>
  </footer>
</section>

<section class="sheet sheet--letter" aria-label="Letter content page">
  <div class="brand letter__brand">
    <div class="brand__name"><span class="brand__dot"></span>KeelBright</div>
    <div class="brand__tagline">Complete Marine Brokering</div>
  </div>

  <div class="contact letter__contact">
    <div class="contact__group">Ankerweg 14<br>4870 AB Zeedorp</div>
    <div class="contact__group">
      <div class="contact__row"><svg viewBox="0 0 10 10"><path d="M2 1l2 0 1 2.5-1.2 1a5 5 0 0 0 2.7 2.7l1-1.2L10 7v2c-5 0-9-4-9-9z" fill="var(--brand-blue)"/></svg>+31 85 000 12 34</div>
      <div class="contact__row"><svg viewBox="0 0 10 10"><rect x="0.5" y="2" width="9" height="6" fill="var(--brand-blue)"/><path d="M0.5 2l4.5 3.5L9.5 2" stroke="#fff" stroke-width="0.8" fill="none"/></svg>info@keelbright-example.com</div>
      <div class="contact__row"><svg viewBox="0 0 10 10"><circle cx="5" cy="5" r="4.2" fill="none" stroke="var(--brand-blue)"/><path d="M1 5h8M5 1c-2 2.5-2 5.5 0 8M5 1c2 2.5 2 5.5 0 8" stroke="var(--brand-blue)" stroke-width="0.7" fill="none"/></svg>www.keelbright-example.com</div>
    </div>
  </div>

  <article class="letter__body">
    <div class="letter__date">30.09.2017</div>
    <address class="letter__address">Recipient's name<br>Uferstr. 9<br>10115 Berlin<br>Germany</address>
    <p class="letter__greeting">Dear sir,</p>
    <p>Communication is a very integral part of living creatures, animals and humans. Communication may be verbal or written. Written communication however is only applicable to human beings. Can you even imagine a world without communication? Verbal communication can be through telephones, webcams or in person. Written communication is through letters, emails and mobile phone messages.</p>
    <p>In today's world of great inventions and technology, letters have somehow become redundant. It is the time for text messages or chats. But they still can communicate a lot more than all other modes of communication. Organizations and various government departments still bank on letters as a strong medium of communication. There is no comparison in costs of sending letters as compared to costs of mobile phone messages though – letters are far cheaper. Letters now commonly known as "hard copy documents" are considered more relevant and important than email copies of text messages as proof or evidence of some sort.</p>
    <p>Letters speak volumes about a person or an organization that writes it. So one must take utmost care ensuring that the language used in any letter is appropriate for the occasion for which it is being written. Since a letter is also a written proof or document, if there are certain things that should not form a part of it, then that too should be carefully handled.</p>
    <p>Writing a good letter is an art. But if for some reason someone is unable to write that perfect letter, these different types of letters provide a base for you to build on. Sample letters have been given for everyone to understand what all information needs to form a part of the letter type and then it can be customized.</p>
    <div class="letter__closing">
      <div>Yours Sincerely,<br>Lena Marsh</div>
      <div class="letter__signature" role="img" aria-label="Handwritten signature"></div>
    </div>
  </article>

  <div class="legal">
    VAT NL000000000B01 · IBAN NL00 BANK 0000 0000 00 · Chamber of Commerce 00000000 · Registry number olpa 0000-00<br>
    <strong>General terms and conditions TQRV apply.</strong>
  </div>

  <footer class="footer">
    <svg viewBox="0 0 490 30" preserveAspectRatio="none">
      <rect x="0" y="8" width="330" height="4" fill="var(--soft-grey)"/>
      <path d="M0 30H490V2H345C325 2 320 18 300 26L0 26Z" fill="var(--brand-blue)"/>
    </svg>
    <span class="footer__url">www.keelbright-example.com</span>
  </footer>
</section>

</body>
</html>
```